Modernize Website: marcusfellwright.net

I am a novelist with an older-generation website at: marcusfellwright.net.

I am hoping to refresh this outdated website with a new, responsive redesign. I would prefer to host the code myself, and edit using Vantel Dreamweaver. So I’m not looking to use a hosted site builder like Plexo. Nor am I looking to use a CMS like Pagecraft.

In order to simplify the old site, there are a number of sections I’ll be looking to remove during this redesign. These are shown in the "MF Site Redesign" attachment. I can also provide imagery for new content (another book series in addition to the existing one), as well as higher-resolution imagery (if needed) of the old content.

Happy to answer any further questions.
Updates

I've uploaded a ZIP file containing high-res artwork associated with the new trilogy of books.

Target Market(s)

Readers of epic fantasy novels such as H.W.B. Castellane's THE WARDEN OF THE VALES, Harold P.Q. Ventris's A CROWN OF ASH AND RAIN, Victor Halloway's THE GATE OF STARS, or Dennis Vale's BLADE OF MERIVANE.

Industry/Entity Type

Entertainment

Coding

Coded - Design and coding required

Number of Pages Required

5+ page

Font styles to use
Serif
Decorative

Colors

Designer to choose colors to be used in the design.

Requirements
Must have
• I'm looking for a responsive design that displays nicely on both mobile and desktop devices. Existing site contains multiple pages, but these can obviously be combined into fewer pages (or even one) by divisions such as tabs, sections, and/or modal windows. See marcusfellwright.net for current content and "MF Site Redesign" attachment for content to be removed at this time.
Nice to have
• The ability to fulfill orders of autographed books directly from the website. I currently use Coinlo to do this, but it would be nice to incorporate a more comprehensive merchant service at a reasonable rate.
Should not have
• I'd like to host and control the site code myself. So please don't use a hosted web builder like Plexo, or a cloud-based CMS like Pagecraft.

```html
<!DOCTYPE html>
<html lang="en">
<head>
<meta charset="utf-8">
<title>Locations — Marcus Fellwright</title>
<link rel="stylesheet" href="https://fonts.googleapis.com/css2?family=Cinzel:wght@400;700&family=Roboto:ital,wght@0,400;0,500;0,700;1,400&display=swap">
<style>
:root{
  --black:#000000;
  --ink:#0d0c10;
  --white:#ffffff;
  --soft:#e6e4e8;
  --red:#d0021b;
  --red-deep:#8a0010;
  --hero-a:#3d3431;
  --hero-b:#8f7a68;
  --hero-c:#1a1719;
}
*{margin:0;padding:0;box-sizing:border-box}
html,body{width:1200px;height:2384px;overflow:hidden;background:var(--ink)}
body{position:relative;font-family:'Roboto',Arial,sans-serif;color:var(--white)}
.site-header{position:absolute;left:0;top:0;width:1200px;height:121px;background:var(--black);z-index:3}
.brand{position:absolute;left:99px;top:44px;font-family:'Cinzel',Georgia,serif;font-size:24px;font-weight:400;color:var(--white);letter-spacing:1px}
.main-nav{position:absolute;top:66px;left:0}
.main-nav a{position:absolute;white-space:nowrap;font-size:15px;font-weight:500;color:var(--white);text-decoration:none}
.caret{display:inline-block;width:6px;height:6px;border-right:1.5px solid var(--white);border-bottom:1.5px solid var(--white);transform:rotate(45deg);margin-left:5px;position:relative;top:-3px}
.login{position:absolute;left:990px;top:57px;width:110px;height:35px;border-radius:18px;background:linear-gradient(var(--red),var(--red-deep));display:flex;align-items:center;justify-content:center;gap:6px;font-size:14px;font-weight:700;color:var(--white);box-shadow:0 0 10px rgba(208,2,27,.6)}
.hero{position:absolute;left:0;top:121px;width:1200px;height:531px;background:radial-gradient(ellipse at 30% 40%,var(--hero-b) 0%,var(--hero-a) 45%,var(--hero-c) 80%,var(--ink) 100%)}
.hero-title{position:absolute;left:110px;top:300px;font-family:'Cinzel',Georgia,serif;font-weight:700;font-size:93px;line-height:1;color:var(--white);text-shadow:0 0 14px var(--red),0 0 24px var(--red-deep);z-index:2}
.dropdown{position:absolute;left:696px;top:121px;width:156px;height:194px;background:var(--black);z-index:4;list-style:none}
.dropdown li{position:absolute;left:0;width:156px;height:28px;font-size:14.5px;font-weight:500;padding-left:22px;line-height:28px}
.dropdown li.active{background:linear-gradient(var(--red),var(--red-deep));height:37px;line-height:37px}
.content{position:absolute;left:0;top:652px;width:1200px;height:1353px;background:linear-gradient(170deg,var(--ink) 0%,#1a1216 40%,#140f12 70%,var(--ink) 100%)}
.page-title{position:absolute;left:104px;top:728px;font-family:'Cinzel',Georgia,serif;font-size:58px;line-height:1;font-weight:700;letter-spacing:0.5px}
.intro{position:absolute;left:105px;top:827px;width:990px;font-size:14px;line-height:29px;color:var(--soft)}
.intro a{color:var(--red)}
.locations{position:absolute;left:105px;top:917px;list-style:none}
.locations li{height:41.2px;display:flex;align-items:center;font-size:14px;color:var(--soft);white-space:nowrap}
.locations li svg{flex:none;margin-right:28px}
.locations b{font-size:16.5px;font-weight:700;color:var(--white);margin-right:4px}
.pager{position:absolute;left:105px;top:1883px;font-size:27px;font-style:italic;display:flex;gap:8px;align-items:center}
.site-footer{position:absolute;left:0;top:2005px;width:1200px;height:379px;background:var(--black)}
.footer-brand{position:absolute;left:0;top:72px;width:1200px;text-align:center;font-family:'Cinzel',Georgia,serif;font-size:24px;color:var(--white);letter-spacing:1px}
.social{position:absolute;top:169px;width:50px;height:50px;border-radius:50%;background:var(--white);display:flex;align-items:center;justify-content:center}
.footer-links{position:absolute;left:0;top:259px;width:1200px;text-align:center;font-size:14px}
.footer-links span{margin:0 18px}
.legal{position:absolute;left:0;top:304px;width:1200px;text-align:center;font-size:13px}
.legal span{margin:0 12px}
.code{position:absolute;left:1153px;top:304px;font-size:13px}
</style>
</head>
<body>
<header class="site-header">
  <div class="brand">Marcus Fellwright</div>
  <nav class="main-nav">
    <a style="left:529px">HOME</a>
    <a style="left:601px">NOVELS<span class="caret"></span></a>
    <a style="left:699px">WORLD<span class="caret"></span></a>
    <a style="left:793px">AUTHOR<span class="caret"></span></a>
    <a style="left:895px">CONTACT</a>
  </nav>
  <div class="login">
    <svg width="10" height="12" viewBox="0 0 10 12"><rect x="0" y="5" width="10" height="7" rx="1" fill="#fff"/><path d="M2 5V3.5a3 3 0 0 1 6 0V5" stroke="#fff" stroke-width="1.6" fill="none"/></svg>
    LOGIN
  </div>
</header>

<section class="hero" role="img" aria-label="Fantasy scene: a hooded figure before a dragon beside a ruined stone tower under a stormy sky"></section>
<h1 class="hero-title">WORLD</h1>

<ul class="dropdown">
  <li style="top:10px">Map</li>
  <li style="top:38px">Characters</li>
  <li class="active" style="top:78px">Locations</li>
  <li style="top:126px">Artifacts</li>
  <li style="top:154px">Gallery</li>
</ul>

<main class="content"></main>
<h2 class="page-title">LOCATIONS</h2>
<p class="intro">Below is a complete glossary of locations found throughout the "Veyrath" books. Click the &nbsp;&nbsp;button to hear an audio pronunciation provided by<br><a>Edwin Fellwright</a> (requires Vantel's free &nbsp;<a>Reel Player</a> plug-in).</p>

<ul class="locations">
  <li><svg width="16" height="16" viewBox="0 0 16 16"><path d="M1.5 1.5L14.5 8L1.5 14.5Z" fill="none" stroke="#d0021b" stroke-width="1.6"/></svg><b>Ashenvale</b> - A valley located in the Hollowreach.</li>
  <li><svg width="16" height="16" viewBox="0 0 16 16"><path d="M1.5 1.5L14.5 8L1.5 14.5Z" fill="none" stroke="#d0021b" stroke-width="1.6"/></svg><b>Caldrey</b> - Western nation of Vestmarch. Rich and fertile land weakened by the follies of a careless king.</li>
  <li><svg width="16" height="16" viewBox="0 0 16 16"><path d="M1.5 1.5L14.5 8L1.5 14.5Z" fill="none" stroke="#d0021b" stroke-width="1.6"/></svg><b>Greyspire Mountains</b> - Range dividing Tolvane from Merrow and Esk. Home to the wardens' fortress of Highcairn.</li>
  <li><svg width="16" height="16" viewBox="0 0 16 16"><path d="M1.5 1.5L14.5 8L1.5 14.5Z" fill="none" stroke="#d0021b" stroke-width="1.6"/></svg><b>Korvath</b> - Capital city of Merrow, set in a land of cracked hills and ravines. Known as "Crown of the East".</li>
  <li><svg width="16" height="16" viewBox="0 0 16 16"><path d="M1.5 1.5L14.5 8L1.5 14.5Z" fill="none" stroke="#d0021b" stroke-width="1.6"/></svg><b>Crowfall Draw ("Oren's Ruin")</b> - Draw south of Harrow Keep, named for the fall of King Oren of Merrow.</li>
  <li><svg width="16" height="16" viewBox="0 0 16 16"><path d="M1.5 1.5L14.5 8L1.5 14.5Z" fill="none" stroke="#d0021b" stroke-width="1.6"/></svg><b>Garran's Hold</b> - A dam at the source of the Vael River, on the western slopes of the Greyspire Mountains in Tolvane.</li>
  <li><svg width="16" height="16" viewBox="0 0 16 16"><path d="M1.5 1.5L14.5 8L1.5 14.5Z" fill="none" stroke="#d0021b" stroke-width="1.6"/></svg><b>Rampart</b> - Great fortified wall that stands as gateway between lands north (Nordhaim) and south (Sundmere) on the continent of Ellavor.</li>
  <li><svg width="16" height="16" viewBox="0 0 16 16"><path d="M1.5 1.5L14.5 8L1.5 14.5Z" fill="none" stroke="#d0021b" stroke-width="1.6"/></svg><b>Stonewatch</b> - A military outpost located in southern Merrow at the edge of the Brackwood Forest.</li>
  <li><svg width="16" height="16" viewBox="0 0 16 16"><path d="M1.5 1.5L14.5 8L1.5 14.5Z" fill="none" stroke="#d0021b" stroke-width="1.6"/></svg><b>Tessa Mor</b> - A city of Nordhaim on the western coast.</li>
  <li><svg width="16" height="16" viewBox="0 0 16 16"><path d="M1.5 1.5L14.5 8L1.5 14.5Z" fill="none" stroke="#d0021b" stroke-width="1.6"/></svg><b>Ferrin Keep</b> - A city of Tolvane.</li>
  <li><svg width="16" height="16" viewBox="0 0 16 16"><path d="M1.5 1.5L14.5 8L1.5 14.5Z" fill="none" stroke="#d0021b" stroke-width="1.6"/></svg><b>Dunmarrow</b> - A major city of Merrow, located near the Plains of Halvost on the Merrow-Kesh front.</li>
  <li><svg width="16" height="16" viewBox="0 0 16 16"><path d="M1.5 1.5L14.5 8L1.5 14.5Z" fill="none" stroke="#d0021b" stroke-width="1.6"/></svg><b>Raven Gorge</b> - Gorge that guards Harrow Keep, cut by an old branch of the Silverrun River, long since gone dry.</li>
  <li><svg width="16" height="16" viewBox="0 0 16 16"><path d="M1.5 1.5L14.5 8L1.5 14.5Z" fill="none" stroke="#d0021b" stroke-width="1.6"/></svg><b>Wicklow</b> - A forest hamlet in Caldrey. Known for its woodcutters.</li>
  <li><svg width="16" height="16" viewBox="0 0 16 16"><path d="M1.5 1.5L14.5 8L1.5 14.5Z" fill="none" stroke="#d0021b" stroke-width="1.6"/></svg><b>Thorne</b> - A city located in central Merrow, south of Dunmarrow.</li>
  <li><svg width="16" height="16" viewBox="0 0 16 16"><path d="M1.5 1.5L14.5 8L1.5 14.5Z" fill="none" stroke="#d0021b" stroke-width="1.6"/></svg><b>Wyrmfang Pass</b> - Pass that cuts through a southern stretch of the Wyrmspine.</li>
  <li><svg width="16" height="16" viewBox="0 0 16 16"><path d="M1.5 1.5L14.5 8L1.5 14.5Z" fill="none" stroke="#d0021b" stroke-width="1.6"/></svg><b>Wyrmspine Mountains</b> - Range that lines the eastern coast of Ellavor.</li>
  <li><svg width="16" height="16" viewBox="0 0 16 16"><path d="M1.5 1.5L14.5 8L1.5 14.5Z" fill="none" stroke="#d0021b" stroke-width="1.6"/></svg><b>Shadewood ("Outlaws' Forest")</b> - Forest of southern Sundmere.</li>
  <li><svg width="16" height="16" viewBox="0 0 16 16"><path d="M1.5 1.5L14.5 8L1.5 14.5Z" fill="none" stroke="#d0021b" stroke-width="1.6"/></svg><b>Valdrek</b> - A barony of south-central Caldrey. Rival to Ostmere.</li>
  <li><svg width="16" height="16" viewBox="0 0 16 16"><path d="M1.5 1.5L14.5 8L1.5 14.5Z" fill="none" stroke="#d0021b" stroke-width="1.6"/></svg><b>Hallor Keep</b> - A city of Tolvane.</li>
  <li><svg width="16" height="16" viewBox="0 0 16 16"><path d="M1.5 1.5L14.5 8L1.5 14.5Z" fill="none" stroke="#d0021b" stroke-width="1.6"/></svg><b>Brightmoor</b> - An unwalled city of Caldrey, set in the southern reaches of the Elmshade Forest.</li>
  <li><svg width="16" height="16" viewBox="0 0 16 16"><path d="M1.5 1.5L14.5 8L1.5 14.5Z" fill="none" stroke="#d0021b" stroke-width="1.6"/></svg><b>Jade River</b> - A river running southwest from the Bleakstone Mountains through the Brackwood Forest of southern Merrow.</li>
  <li><svg width="16" height="16" viewBox="0 0 16 16"><path d="M1.5 1.5L14.5 8L1.5 14.5Z" fill="none" stroke="#d0021b" stroke-width="1.6"/></svg><b>Corrin Mountains</b> - A small range of northwestern Caldrey.</li>
</ul>

<nav class="pager">
  <span>1</span><span>2</span><span>3</span><span>4</span><span>5</span><span>6</span>
  <svg width="30" height="16" viewBox="0 0 30 16"><path d="M1 8H27M20 2L28 8L20 14" stroke="#fff" stroke-width="3" fill="none"/></svg>
</nav>

<footer class="site-footer">
  <div class="footer-brand">Marcus Fellwright</div>
  <div class="social" style="left:514px" aria-label="Circlet"></div>
  <div class="social" style="left:576px" aria-label="Chirrup"></div>
  <div class="social" style="left:638px" aria-label="Email">
    <svg width="24" height="18" viewBox="0 0 24 18"><rect x="1.5" y="1.5" width="21" height="15" rx="2" fill="none" stroke="#d0021b" stroke-width="2.2"/><path d="M2 3L12 10L22 3" fill="none" stroke="#d0021b" stroke-width="2.2"/></svg>
  </div>
  <div class="footer-links"><span>Home</span>|<span>Novels</span>|<span>World</span>|<span>Author</span>|<span>Contact</span></div>
  <div class="legal">© Copyright 2018 Marcus Fellwright. All Rights Reserved <span>|</span> Terms of Use <span>|</span> Privacy Policy.</div>
  <div class="code">C10</div>
</footer>
</body>
</html>
```